Construction company business card

One side to be the logo with the company name, The other side I would like: (Tomas verbick) Project manager 41 barrow crescent brennock 52917306224783(03) 9703 2428Info@gudeljgroup.comAnd then maybe a couple dot points saying what we do:Construction (commercial & industrial) Civil construction

Anything else please contact me!
Maybe curved st one edge of the card

Target Market(s)

Older clientele

Industry/Entity Type

Construction Company

Contact Information for Business Card

Read above

Colors
3277b5
1b1b1b
9d9d9d

Requirements
Must have
• Use my logo on one side
Nice to have
• Read above
Should not have
• Read above

```html
<!DOCTYPE html>
<html lang="en">
<head>
<meta charset="utf-8">
<title>Ironvale Property Group – Business Card</title>
<link href="https://fonts.googleapis.com/css2?family=Open+Sans:wght@400;600;700&display=swap" rel="stylesheet">
<style>
  :root {
    --brand-blue: #3277b5;
    --brand-black: #1b1b1b;
    --brand-grey: #9d9d9d;
    --text-grey: #6f6f6f;
    --card-white: #ffffff;
    --navy-top: #2e3d4b;
    --navy-bottom: #15202b;
    --stage: #161616;
  }
  * { box-sizing: border-box; margin: 0; padding: 0; }
  html, body {
    width: 1200px;
    height: 900px;
    overflow: hidden;
    background: var(--stage);
    font-family: "Open Sans", Arial, sans-serif;
  }
  .canvas {
    position: relative;
    width: 1200px;
    height: 900px;
  }
  .card {
    position: absolute;
    left: 320px;
    width: 560px;
    height: 320px;
    border-radius: 26px;
    overflow: hidden;
  }

  /* Logo side */
  .card-front {
    top: 90px;
    background: linear-gradient(160deg, var(--navy-top) 0%, var(--navy-bottom) 100%);
  }
  .brand-lockup {
    position: absolute;
    top: 70px;
    left: 0;
    right: 0;
    display: flex;
    flex-direction: column;
    align-items: center;
    gap: 14px;
    color: var(--brand-blue);
  }
  .brand-mark {
    width: 64px;
    height: 64px;
    border-radius: 50%;
    background: var(--brand-blue);
  }
  .brand-name {
    font-weight: 700;
    font-size: 30px;
    letter-spacing: 1px;
    text-transform: uppercase;
    line-height: 1;
  }
  .brand-tagline {
    font-weight: 700;
    font-size: 14px;
    letter-spacing: 4px;
    text-transform: uppercase;
    line-height: 1;
    margin-top: -6px;
  }
  .services {
    position: absolute;
    left: 34px;
    bottom: 30px;
    display: flex;
    gap: 10px;
    list-style: none;
    color: #e6e9ec;
    font-size: 14px;
  }
  .services li::before {
    content: "";
    display: inline-block;
    width: 7px;
    height: 7px;
    border-radius: 50%;
    background: var(--brand-blue);
    margin-right: 5px;
    vertical-align: middle;
  }

  /* Contact side */
  .card-back {
    top: 480px;
    background: var(--card-white);
  }
  .card-back .brand-lockup {
    top: 90px;
    left: 30px;
    right: auto;
    width: 250px;
  }
  .divider {
    position: absolute;
    left: 300px;
    top: 28px;
    width: 1px;
    height: 264px;
    background: linear-gradient(to bottom, transparent, #d4d4d4 30%, #d4d4d4 70%, transparent);
  }
  .contact {
    position: absolute;
    left: 324px;
    top: 58px;
    color: var(--text-grey);
    font-size: 15px;
    line-height: 1.3;
  }
  .contact-name {
    color: var(--brand-blue);
    font-weight: 600;
    font-size: 18px;
    text-transform: uppercase;
  }
  .contact-role { margin-bottom: 10px; }
  .contact-line {
    display: flex;
    align-items: center;
    gap: 6px;
  }
  .contact-line svg {
    width: 12px;
    height: 12px;
    fill: var(--brand-blue);
    flex: none;
  }
</style>
</head>
<body>
<main class="canvas">

  <section class="card card-front" aria-label="Card front">
    <div class="brand-lockup">
      <span class="brand-mark"></span>
      <span class="brand-name">Ironvale</span>
      <span class="brand-tagline">Property Group</span>
    </div>
    <ul class="services">
      <li>Construction (commercial &amp; industrial)</li>
      <li>Civil construction</li>
    </ul>
  </section>

  <section class="card card-back" aria-label="Card back">
    <div class="brand-lockup">
      <span class="brand-mark"></span>
      <span class="brand-name">Ironvale</span>
      <span class="brand-tagline">Property Group</span>
    </div>
    <span class="divider"></span>
    <div class="contact">
      <p class="contact-name">Tomas Verbick</p>
      <p class="contact-role">Project manager</p>
      <p class="contact-address">41 barrow crescent<br>brennock 5291</p>
      <p>7306224783</p>
      <p class="contact-line">
        <svg viewBox="0 0 24 24" aria-hidden="true"><path d="M6.6 10.8a15.1 15.1 0 0 0 6.6 6.6l2.2-2.2c.3-.3.7-.4 1-.2 1.1.4 2.3.6 3.6.6.6 0 1 .4 1 1V20c0 .6-.4 1-1 1A17 17 0 0 1 3 4c0-.6.4-1 1-1h3.5c.6 0 1 .4 1 1 0 1.3.2 2.5.6 3.6.1.3 0 .7-.2 1z"/></svg>
        <span>7306224783</span>
      </p>
      <p class="contact-line">
        <svg viewBox="0 0 24 24" aria-hidden="true"><path d="M7 1h10a2 2 0 0 1 2 2v18a2 2 0 0 1-2 2H7a2 2 0 0 1-2-2V3a2 2 0 0 1 2-2zm0 3v14h10V4zm5 15.5a1.2 1.2 0 1 0 0 2.4 1.2 1.2 0 0 0 0-2.4z"/></svg>
        <span>(03) 9418 6573</span>
      </p>
      <p class="contact-line">
        <svg viewBox="0 0 24 24" aria-hidden="true"><path d="M2 5h20v14H2zm2 2v.5l8 5 8-5V7zm0 2.8V17h16V9.8l-8 5z"/></svg>
        <span>Info@verbickgroup.com</span>
      </p>
    </div>
  </section>

</main>
</body>
</html>
```